Tarlow Plumbing & Heating Limited needs a service and maintenance contract document design

Tarlow Plumbing & Heating Limited are a well established family owned and operated company.

We currently offer installation, service and repair services for gas, plumbing, heating and electrical work. We wish to offer service and maintenance plans for plumbing, heating and electrical for our domestic clients in the UK. We would like the brochure to incorporate our company logo and colours, and reflect the reliable, quality, 5 star service we offer our clients.
I have attached a brochure that a friends company uses to give a good idea of the structure of the plans we wish to offer. We want to give our customers a choice in what packages best suit their needs. However, the pricing structure and certain elements/content of what we offer will be slightly different due to our geographical location.

We would like to have the basic structure of the brochure put in place and the
text content editable to our specific needs. Looking for advice on this but we do have Acrobat DC if we need to edit the text ourselves?

We use our logo with "TARLOW" in white over a grey backgound.

Our website is - www.tarlow.plumbing
Facebook and twitter handle is - @TarlowHeating

Target Market(s)

UK domestic plumbing, heating, natural gas, LPG and electrical market. Both private homeowners and landlords. Please see both the domestic and landlord document files attached for an idea on what we'd like.

Colors

Designer to choose colors to be used in the design.

Requirements
Must have
• Would like the finished design to incorporate the branding and colours we already use. Professional, Contemporary designs that will stand out above our competition.
• The content of the brochures MUST be very similar in structure to the files I’ve attached to the brief.
• We are having many designs submitted that are just copying our website content. This is not what we are asking for.
• I would like the icons etc to be redesigned so they are ours and not copied.
• Please also see the Landlords brochure attached to the brief. We would like this to be a separate document but to reflect the same design as the homeowner design you submit.
• The content of the documents will need to be re worded for our own use but I'm happy to change this once the design element is in place.
• A4 sized pages as per the example I've attached
• Must be able to attach the document to our website for clients to download.
Nice to have
• A4 sized pages as per the examples I've attached
Should not have
• Please DO NOT copy the content from our website to create our service plan brochures. This is not what we are after. As above, we need the brochures to be like the ones we've provided but made to fit our brand.
• Thank you

```html
<!DOCTYPE html>
<html lang="en">
<head>
<meta charset="utf-8">
<title>Tarlow Plumbing &amp; Heating – Services</title>
<link href="https://fonts.googleapis.com/css2?family=Montserrat:wght@300;400;600;700&display=swap" rel="stylesheet">
<style>
  :root {
    --orange: #f7931e;
    --blue: #1a6fc0;
    --panel-blue: #7ba7d9;
    --white: #ffffff;
    --page-bg: #ffffff;
    --canvas-bg: #f2f2f2;
  }
  * { margin: 0; padding: 0; box-sizing: border-box; }
  html, body { width: 1200px; height: 1200px; overflow: hidden; background: var(--canvas-bg); font-family: 'Montserrat', sans-serif; }
  .page { position: absolute; left: 196px; top: 28px; width: 806px; height: 1142px; background: var(--page-bg); }
  .hero { position: absolute; left: 49px; top: 49px; width: 709px; height: 431px; background: var(--orange); border-radius: 30px; overflow: hidden; }
  .hero-title { position: absolute; left: 34px; top: 30px; color: var(--white); font-weight: 700; font-size: 48px; line-height: 50px; letter-spacing: 0.3px; }
  .hero-tagline { position: absolute; left: 34px; top: 164px; color: var(--blue); font-size: 31.5px; font-weight: 300; line-height: 40px; white-space: nowrap; }
  .hero-tagline strong { font-weight: 600; }
  .hero-values { position: absolute; left: 34px; top: 203px; color: var(--blue); font-size: 31px; font-weight: 300; line-height: 40px; white-space: nowrap; opacity: 0.85; }
  .service-icons { position: absolute; left: 0; top: 292px; width: 709px; height: 80px; }
  .service-icons svg { position: absolute; top: 0; width: 80px; height: 80px; fill: none; stroke: var(--white); stroke-width: 2.4; stroke-linecap: round; stroke-linejoin: round; }
  .specialisms { position: absolute; left: 49px; top: 505px; width: 225px; height: 480px; background: var(--panel-blue); border-radius: 26px; color: var(--white); padding: 42px 24px 0 21px; }
  .specialisms h2 { font-size: 18.5px; font-weight: 600; letter-spacing: 0.2px; margin-bottom: 24px; white-space: nowrap; }
  .specialisms ul { list-style: none; font-size: 16px; font-weight: 300; line-height: 19.6px; }
  .specialisms li { position: relative; padding-left: 14px; }
  .specialisms li::before { content: "·"; position: absolute; left: 0; }
  .photo { position: absolute; width: 228px; height: 228px; border-radius: 26px; }
  .photo-water { left: 290px; top: 505px; background: radial-gradient(circle at 50% 55%, #9fd3ea, #3f7fa3 75%, #2c5f80); }
  .photo-flame { left: 533px; top: 505px; background: radial-gradient(ellipse at 60% 60%, #3aa6ff, #1a2f8a 45%, #05081c 80%); }
  .photo-thermostat { left: 290px; top: 757px; background: linear-gradient(135deg, #f1e7e6, #e3dcdc 60%, #cfc4c0); }
  .photo-tap { left: 533px; top: 757px; background: linear-gradient(90deg, #f4f4f4, #8e8e8e 45%, #2e2e2e 70%, #9a9a9a); }
  .cta { position: absolute; left: 0; top: 1026px; width: 806px; text-align: center; color: var(--blue); }
  .cta-small { font-size: 15px; font-weight: 300; letter-spacing: 13px; margin-left: 13px; }
  .cta-large { font-size: 25px; font-weight: 700; margin-top: 2px; }
  .page-footer { position: absolute; left: 49px; top: 1079px; font-size: 12px; font-weight: 600; }
  .page-number { color: var(--blue); margin-right: 10px; }
  .page-site { color: var(--orange); }
</style>
</head>
<body>
  <main class="page">
    <section class="hero">
      <h1 class="hero-title">FRIENDLY, FAMILY RUN<br>COMPANY</h1>
      <p class="hero-tagline">Your Local <strong>Plumbing &amp; Heating Experts</strong></p>
      <p class="hero-values">Local - Professional- Reliable - Trusted</p>
      <div class="service-icons">
        <svg style="left:57px" viewBox="0 0 80 80" aria-label="Pipe icon"><path d="M8 6h22v8H8zM12 14v38a16 16 0 0 0 32 0v-6h14v-8H38v14a4 4 0 0 1-8 0V14"/><path d="M58 32h8v20M66 58c-3 4-3 7 0 8 3-1 3-4 0-8z"/></svg>
        <svg style="left:191px" viewBox="0 0 80 80" aria-label="Engineer icon"><path d="M26 22a14 12 0 0 1 28 0zM22 22h36M30 24v8a10 10 0 0 0 20 0v-8"/><path d="M20 62c0-10 8-16 20-16s20 6 20 16"/><path d="M8 66a6 6 0 0 1 10-4h44a6 6 0 1 1 0 8H18a6 6 0 0 1-10-4z"/></svg>
        <svg style="left:331px" viewBox="0 0 80 80" aria-label="Thermostat icon"><rect x="8" y="6" width="42" height="58" rx="3"/><rect x="14" y="12" width="30" height="12"/><path d="M16 32h2M24 32h2M32 32h2M16 40h2M16 48h2M24 48h2"/><path d="M40 44v-8a3 3 0 0 1 6 0v12l8-2a4 4 0 0 1 5 4l6 12c2 5 2 8 2 12"/></svg>
        <svg style="left:455px" viewBox="0 0 80 80" aria-label="Washing machine icon"><rect x="22" y="6" width="52" height="56"/><path d="M28 12h4M36 12h4M44 12h4"/><circle cx="48" cy="38" r="14"/><circle cx="48" cy="38" r="7"/><path d="M22 58c-12 0-16 4-16 8s8 6 18 6 18-3 18-6"/></svg>
        <svg style="left:585px" viewBox="0 0 80 80" aria-label="Water heater icon"><path d="M14 8h52v52a4 4 0 0 1-4 4H18a4 4 0 0 1-4-4z"/><circle cx="40" cy="48" r="4"/><path d="M32 56h16M32 64v8M48 64v8M14 16h52"/></svg>
      </div>
    </section>

    <section class="specialisms">
      <h2>WE SPECIALISE IN</h2>
      <ul>
        <li>Central Heating Systems</li>
        <li>Boiler Installation</li>
        <li>Boiler Servicing &amp; Repairs</li>
        <li>Boiler Care Plans</li>
        <li>General Plumbing</li>
        <li>Bathrooms</li>
        <li>Power Flushing</li>
        <li>Underfloor Heating</li>
        <li>LPG</li>
      </ul>
    </section>

    <div class="photo photo-water" role="img" aria-label="Close-up of a water droplet splash"></div>
    <div class="photo photo-flame" role="img" aria-label="Blue gas flame on a burner ring"></div>
    <div class="photo photo-thermostat" role="img" aria-label="Hand adjusting a wall-mounted digital thermostat"></div>
    <div class="photo photo-tap" role="img" aria-label="Chrome kitchen tap with running water"></div>

    <div class="cta">
      <p class="cta-small">Contact us</p>
      <p class="cta-large">TO LEARN MORE</p>
    </div>

    <footer class="page-footer"><span class="page-number">2</span><span class="page-site">| tarlow.plumbing</span></footer>
  </main>
</body>
</html>
```